Naturopath needs product label for new essence range

I need a label design for a new range of Essences. The essences resonate with the energetic chakra centres of the body to shift blockages, balance them and lead to transformation and spiritual growth. I have a logo to be used. The name of the essence range is Veronel which means "to reveal truth or True Nature". The first essence resonates with the Base Chakra and is called "Base" I would like a strong bold red colour to feature in the design. The label size would be about 76mm x 27mm. See below for the required information to be on the label.
Updates

Hi everyone, I'm not sure if it's important to help with the design, but I've just uploaded the logo in several different formats. Thanks for all your submissions. Also please use a deep red colour, the example from the colour wheel is too light. Kind regards, Brent

Target Market(s)

Adults open to alternative therapies and spiritual development

Industry/Entity Type

Product

Colors
eb1f27

Requirements
Must have
• The logo. A deep red colour as the background or part of the background
"Base"
veronelessences.com.au
Batch
Expiry
Ingredients: vibrational essence of herbs, flowers and crystals, purified water, brandy (approx 12.5% alcohol)
20ml
Dosage: 7 drops once a day

```html
<!DOCTYPE html>
<html lang="en">
<head>
<meta charset="utf-8">
<title>Veronel Essences – Base label</title>
<link rel="stylesheet" href="https://fonts.googleapis.com/css2?family=Cinzel:wght@400;500&family=Montserrat:wght@300;400;600&display=swap">
<style>
  :root {
    --label-red: #ec1f2b;
    --ribbon-dark: #140406;
    --ribbon-mid: #5e0a12;
    --gold: #d9a82e;
    --gold-light: #f3d27a;
    --white: #ffffff;
    --page: #ffffff;
  }
  * { box-sizing: border-box; margin: 0; padding: 0; }
  html, body { width: 1200px; height: 1200px; overflow: hidden; background: var(--page); }
  .canvas { position: relative; width: 1200px; height: 1200px; }
  .label {
    position: absolute; left: 388px; top: 58px; width: 383px; height: 1076px;
    background: var(--label-red); color: var(--white);
    font-family: "Montserrat", Arial, sans-serif;
  }
  .ribbon { position: absolute; left: 90px; top: 0; width: 203px; height: 340px; }
  .brand-mark {
    position: absolute; left: 90px; top: 200px; width: 203px; text-align: center;
    font-family: "Cinzel", Georgia, serif; font-weight: 500; font-size: 24px;
    letter-spacing: 3px; color: var(--gold);
  }
  .brand-name {
    position: absolute; left: 0; top: 400px; width: 100%; text-align: center;
    font-family: "Cinzel", Georgia, serif; font-weight: 400; font-size: 39px;
    letter-spacing: 5px; line-height: 1;
  }
  .range-line {
    position: absolute; left: 0; top: 506px; width: 100%;
    display: flex; align-items: center; justify-content: center; gap: 12px;
    font-family: "Cinzel", Georgia, serif; font-size: 20px; letter-spacing: 4px; line-height: 1;
  }
  .gold-rule {
    display: block; height: 2px;
    background: linear-gradient(90deg, transparent, var(--gold) 30%, var(--gold-light) 50%, var(--gold) 70%, transparent);
  }
  .range-line .gold-rule { width: 72px; }
  .product-name {
    position: absolute; left: 0; top: 532px; width: 100%; text-align: center;
    font-family: "Cinzel", Georgia, serif; font-weight: 500; line-height: 1;
    font-size: 104px; letter-spacing: 4px;
  }
  .product-name .small { font-size: 82px; }
  .rule-top { position: absolute; left: 47px; top: 651px; width: 288px; }
  .rule-bottom { position: absolute; left: 47px; top: 698px; width: 288px; }
  .website {
    position: absolute; left: 0; top: 664px; width: 100%; text-align: center;
    font-weight: 300; font-size: 20px; letter-spacing: 1px;
  }
  .volume {
    position: absolute; left: 0; top: 742px; width: 100%; text-align: center;
    font-weight: 300; font-size: 19px; letter-spacing: 1px;
  }
  .details { position: absolute; left: 48px; top: 834px; width: 300px; font-size: 16px; line-height: 1.1; letter-spacing: 0.5px; }
  .details h3 { font-weight: 600; font-size: 16px; letter-spacing: 1px; }
  .details p { font-weight: 400; }
  .dosage { margin-top: 22px; }
  .batch { margin-top: 42px; }
  .expiry { margin-top: 13px; }
</style>
</head>
<body>
<div class="canvas">
  <div class="label">
    <svg class="ribbon" viewBox="0 0 203 340" aria-hidden="true">
      <defs>
        <linearGradient id="ribbonShade" x1="0" x2="1" y1="0" y2="0">
          <stop offset="0" stop-color="var(--ribbon-dark)"/>
          <stop offset="0.5" stop-color="var(--ribbon-mid)"/>
          <stop offset="1" stop-color="var(--ribbon-dark)"/>
        </linearGradient>
      </defs>
      <path d="M0 0 H203 V322 Q101 345 0 322 Z" fill="url(#ribbonShade)"/>
    </svg>
    <div class="brand-mark">VERONEL</div>

    <h1 class="brand-name">VERONEL</h1>
    <div class="range-line"><span class="gold-rule"></span>ESSENCES<span class="gold-rule"></span></div>
    <h2 class="product-name">B<span class="small">AS</span>E</h2>

    <span class="gold-rule rule-top"></span>
    <div class="website">veronelessences.com.au</div>
    <span class="gold-rule rule-bottom"></span>

    <div class="volume">20ml</div>

    <div class="details">
      <h3>Ingredients:</h3>
      <p>vibrational essence of herbs, flowers and crystals, purified water, brandy (approx 12.5% alcohol)</p>
      <h3 class="dosage">Dosage:</h3>
      <p>7 drops once a day</p>
      <h3 class="batch">Batch:</h3>
      <h3 class="expiry">Expiry:</h3>
    </div>
  </div>
</div>
</body>
</html>
```